Technical Proposal

I have a word document that I would like to make look neat, it will be used for a presentation

Target Market(s)

Information Security or Cyber Security

Industry/Entity Type

Information Technology

Requirements
Must have
• Nice formating and theme to match
Nice to have
• Must look elegant as it will be used as a presentation
Should not have
• Please keep the theme consistent and engaging, should not have random colours

```html
<!DOCTYPE html>
<html lang="en">
<head>
<meta charset="utf-8">
<title>Technical Proposal Cover</title>
<link href="https://fonts.googleapis.com/css2?family=Roboto:wght@500;700;900&display=swap" rel="stylesheet">
<style>
  :root {
    --navy: #1b2b80;
    --band: #0f2470;
    --grey: #6b6b6b;
    --globe-rim: #7d95d6;
    --globe-mid: #a9bbe6;
    --globe-core: #f4f7fd;
    --sky: #e4e9f5;
    --sky-soft: #eef1f9;
    --paper: #ffffff;
  }
  * { margin: 0; padding: 0; box-sizing: border-box; }
  html, body {
    width: 847px;
    height: 1200px;
    overflow: hidden;
    background: var(--paper);
  }
  .cover {
    position: relative;
    width: 847px;
    height: 1200px;
    background: var(--paper);
    font-family: "Roboto", Arial, sans-serif;
    overflow: hidden;
  }
  .cover__hero {
    position: absolute;
    left: 0;
    top: 0;
    width: 847px;
    height: 760px;
    background:
      radial-gradient(circle 150px at 540px 340px, rgba(255,255,255,0.95) 0%, rgba(255,255,255,0.55) 55%, rgba(255,255,255,0) 100%),
      radial-gradient(circle 340px at 600px 300px, var(--globe-core) 0%, var(--globe-mid) 62%, var(--globe-rim) 88%, rgba(125,149,214,0.35) 96%, rgba(228,233,245,0) 100%),
      radial-gradient(ellipse 260px 300px at 110px 260px, rgba(255,255,255,0.7) 0%, rgba(255,255,255,0) 100%),
      linear-gradient(180deg, var(--sky) 0%, var(--sky-soft) 55%, var(--paper) 100%);
  }
  .cover__hero::after {
    content: "";
    position: absolute;
    left: 0;
    bottom: 0;
    width: 100%;
    height: 200px;
    background: linear-gradient(180deg, rgba(255,255,255,0) 0%, var(--paper) 100%);
  }
  .cover__title {
    position: absolute;
    top: 792px;
    left: 0;
    width: 100%;
    text-align: center;
    color: var(--navy);
    font-weight: 700;
    font-size: 52px;
    line-height: 52px;
    letter-spacing: 0.5px;
  }
  .cover__subtitle {
    position: absolute;
    top: 853px;
    left: 0;
    width: 100%;
    text-align: center;
    color: var(--grey);
    font-weight: 500;
    font-size: 35px;
    line-height: 36px;
    letter-spacing: 0.5px;
  }
  .brand {
    position: absolute;
    top: 1000px;
    left: 0;
    width: 100%;
    height: 70px;
    display: flex;
    justify-content: center;
    align-items: center;
    gap: 22px;
  }
  .brand__mark {
    width: 58px;
    height: 58px;
    background: var(--navy);
  }
  .brand__name {
    color: var(--navy);
    font-weight: 700;
    font-size: 33px;
    letter-spacing: 1px;
    text-transform: uppercase;
  }
  .cover__band {
    position: absolute;
    left: 0;
    bottom: 0;
    width: 100%;
    height: 32px;
    background: var(--band);
  }
</style>
</head>
<body>
  <main class="cover">
    <div class="cover__hero" role="img" aria-label="Cyber security illustration: a glowing digital padlock in front of a wireframe network globe, in soft blue and white tones"></div>
    <h1 class="cover__title">PROJECT TITLE HERE</h1>
    <p class="cover__subtitle">SUBTEXT HERE</p>
    <div class="brand">
      <span class="brand__mark"></span>
      <span class="brand__name">Northwind Secure Systems</span>
    </div>
    <div class="cover__band"></div>
  </main>
</body>
</html>
```